"Tandem Mouthguards " Custom-made Mouthguard Business Website

We need an informational website for our mouthguard Business "Tandem Mouthguards". The logo is navy blue/lime green so want to have colour scheme that goes nicely with this - have uploaded our mouthguard flyer with some information we need to put into the website but I do have more information to put in there.

Target Market(s)

Sports clubs, sportspeople, parents and kids, schools

Industry/Entity Type

Dental, Custom-made Sports Mouthguards

Coding

Coded - Design and coding required

Number of Pages Required

5+ page

Font styles to use
Serif
Sans Serif

Colors
0054AA
0677BA
7BADD7
CADEEF
E8F1F8
0094D4
00A9DD
6FCCEA
C7EBF8
E9F6FB
00AB8E
00BBA5
67D7C9
C6EFE9
E9F9F6
59FF00
82FF00
B8FF75
E3FFCB
F4FFEA
FFF300
FFF600
FEFA6F
FFFEC7
FFFEE8
FFC000
F8CF3A
FAE287
FDF2CF
FEFAEE
F0912C
F2A743
F7CA91
FBE8D2
FDF5EE
EE7325
F08F49
F5BC92
FAE3D3
FDF4ED

Requirements
Must have
• I want drop down pages, not one scrolling page. Different pages for each heading . Content uploaded - We need a general home page with lots of pictures and info that I'll provide. A page each dedicated to 1) About Us 2) Why choose a custom mouthguard? 3) Gallery 4) Contact Us. Will need logos from "Velora"
Nice to have
• Mainly use greens and blues, but happy to pop in some yellow/oranges/red oranges if it looks good

```html
<!DOCTYPE html>
<html lang="en">
<head>
<meta charset="utf-8">
<title>Tandem Mouthguards – Custom-Made Sports Mouthguards in Perth</title>
<link href="https://fonts.googleapis.com/css2?family=Audiowide&family=Roboto:wght@400;500;700&display=swap" rel="stylesheet">
<style>
:root{
  --navy:#0b1f6b;
  --navy-deep:#0a1a5c;
  --green:#34c83a;
  --green-bright:#59ff00;
  --orange:#ee5f24;
  --text:#2b2b2b;
  --white:#ffffff;
  --sky:#4fb3e6;
}
*{margin:0;padding:0;box-sizing:border-box}
html,body{width:1200px;height:3157px;overflow:hidden}
body{position:relative;font-family:"Roboto",sans-serif;color:var(--text);background:var(--white)}
.abs{position:absolute}
.display{font-family:"Audiowide",sans-serif;color:var(--navy);text-transform:uppercase;letter-spacing:1px;font-weight:400}

/* header */
.top-rule{left:0;top:0;width:1200px;height:5px;background:var(--green)}
.brand{left:143px;top:26px;font-weight:700;color:var(--navy);font-size:34px;line-height:35px}
.brand small{display:block;font-size:9px;line-height:12px;color:var(--green);letter-spacing:1.3px;font-weight:500}
.nav{left:480px;top:0;height:108px;display:flex;align-items:center;font-size:13px;font-weight:500;color:var(--navy)}
.nav a{color:inherit;text-decoration:none;margin-right:32px}
.nav .active{background:var(--green);color:var(--white);width:69px;height:108px;border-radius:0 0 34px 34px;display:flex;align-items:center;justify-content:center;margin-right:18px}

/* hero */
.hero-bg{left:0;top:5px;width:1200px;height:700px;background:
  radial-gradient(ellipse 420px 300px at 330px 430px,rgba(230,214,205,.55),rgba(255,255,255,0) 70%),
  radial-gradient(ellipse 360px 260px at 120px 330px,rgba(214,200,190,.5),rgba(255,255,255,0) 70%),
  linear-gradient(180deg,#eef2f3 0%,#e7ecee 55%,#ffffff 100%)}
.hero-title{left:142px;top:210px;font-size:26px;line-height:44px}
.hero-title span{display:block;border-bottom:2px solid var(--green);width:508px}
.hero-title span:last-child{border:none}
.hero-sub{left:142px;top:362px;font-size:20px;color:#333}
.btn{background:var(--orange);color:var(--white);font-weight:500;font-size:16px;border-radius:34px;display:flex;align-items:center;justify-content:center;text-transform:uppercase}
.dots{left:143px;top:569px;display:flex;gap:13px}
.dots i{width:9px;height:9px;border-radius:50%;background:#c9c9c9}
.dots i:first-child{background:var(--green)}

/* why */
.section-title{left:0;width:1200px;text-align:center;font-size:30px}
.section-title span{display:inline-block;padding:0 12px 10px;border-bottom:2px solid var(--green)}
.feature{width:240px;text-align:center;font-size:19px;line-height:26px;color:#333}
.feature .ring{width:168px;height:168px;margin:0 auto 26px;border-radius:50%;border:3px solid var(--green);display:flex;align-items:center;justify-content:center;background:var(--white);box-shadow:0 4px 0 var(--green)}
.feature .ring.orange{border-color:#f2a743;box-shadow:0 4px 0 var(--orange)}
.arrow{width:32px;height:32px;border-radius:50%;border:2px solid #aaa;display:flex;align-items:center;justify-content:center}

/* about */
.about-title{left:154px;top:1298px;font-size:30px;color:var(--white)}
.about-rule{left:142px;top:1342px;width:250px;height:2px;background:var(--green-bright)}
.about-copy{left:142px;top:1376px;width:500px;color:var(--white);font-size:15.5px;line-height:29px;text-align:justify}

/* gallery */
.tile{width:296px;height:282px;border-radius:15px}

/* footer */
.foot-info{top:2803px;display:flex;align-items:center;gap:14px;color:var(--white);font-size:14px;line-height:20px}
.foot-info .ic{width:40px;height:40px;border-radius:50%;background:var(--white);display:flex;align-items:center;justify-content:center;flex:none}
.foot-info .ic.hot{background:var(--orange)}
.foot-nav{left:0;top:2884px;width:1200px;text-align:center;color:var(--white);font-weight:700;font-size:18px}
.foot-nav span{margin:0 22px;font-weight:400}
.legal{left:0;top:2950px;width:1200px;text-align:center;color:var(--white);font-size:15px}
.social{left:492px;top:3008px;display:flex;gap:10px}
.social i{width:35px;height:35px;border-radius:50%;border:2px solid var(--white);display:block}
.partner{left:0;top:3082px;width:1200px;text-align:center;color:var(--sky);font-weight:700;font-size:17px}
</style>
</head>
<body>

<div class="abs hero-bg" role="img" aria-label="Soft faded photo of a smiling person fitting a clear mouthguard"></div>
<div class="abs top-rule"></div>

<div class="abs brand">TANDEM<br>MOUTHGUARDS<small>CUSTOM-FIT PROTECTION FOR EVERY SMILE</small></div>

<nav class="abs nav">
  <a class="active">HOME</a>
  <a>ABOUT US</a>
  <a>OUR MOUTHGUARDS</a>
  <a>GALLERY</a>
  <a>FAQ</a>
  <a>CONTACT</a>
</nav>

<h1 class="abs display hero-title">
  <span>Tandem Mouthguards</span>
  <span>Custom-Made Sports</span>
  <span>Mouthguards in Perth</span>
</h1>
<p class="abs hero-sub">Protect your smile with a comfortable, professional fit.</p>
<div class="abs btn" style="left:143px;top:428px;width:189px;height:67px">Book Now</div>
<div class="abs dots"><i></i><i></i><i></i><i></i></div>

<svg class="abs" style="left:700px;top:120px" width="460" height="480" viewBox="0 0 460 480">
  <path d="M150 460 A215 215 0 0 0 430 280" fill="none" stroke="#34c83a" stroke-width="5"/>
  <path d="M160 470 A226 226 0 0 0 440 290" fill="none" stroke="#34c83a" stroke-width="4"/>
  <circle cx="225" cy="220" r="198" fill="#fff" stroke="#0b1f6b" stroke-width="30"/>
</svg>
<div class="abs" role="img" aria-label="Photo of two kids in footy jerseys holding a football and wearing coloured mouthguards" style="left:769px;top:184px;width:312px;height:312px;border-radius:50%;background:
  radial-gradient(circle at 72% 52%,#e8c43a 0,#e8c43a 9%,rgba(232,196,58,0) 20%),
  radial-gradient(circle at 32% 38%,#f1cdb8 0,rgba(241,205,184,0) 18%),
  radial-gradient(circle at 82% 30%,#efc8b2 0,rgba(239,200,178,0) 16%),
  radial-gradient(circle at 30% 78%,#3b44b8 0,rgba(59,68,184,0) 30%),
  radial-gradient(circle at 85% 78%,#2d3ea8 0,rgba(45,62,168,0) 28%),
  linear-gradient(180deg,#6f9c4a 0%,#4f8a35 50%,#3f7a2d 100%)"></div>
<div class="abs" role="img" aria-label="Pile of colourful mouthguards in red, rainbow, chequered and blue cases" style="left:478px;top:445px;width:417px;height:185px;border-radius:48% 52% 40% 44% / 60% 55% 45% 40%;background:
  radial-gradient(ellipse at 15% 60%,#d3262a 0,#d3262a 18%,rgba(211,38,42,0) 34%),
  radial-gradient(ellipse at 40% 30%,#f2eef6 0,#dcd6e8 14%,rgba(220,214,232,0) 30%),
  radial-gradient(ellipse at 43% 78%,#2a2a2a 0,#8a8a8a 10%,rgba(138,138,138,0) 24%),
  radial-gradient(ellipse at 65% 45%,#4f8fd8 0,#7fb2e6 18%,rgba(127,178,230,0) 34%),
  radial-gradient(ellipse at 72% 20%,#e9622a 0,#f2b23a 8%,rgba(242,178,58,0) 20%),
  radial-gradient(ellipse at 68% 80%,#b55bc6 0,rgba(181,91,198,0) 22%),
  radial-gradient(ellipse at 88% 70%,#3fc7b0 0,rgba(63,199,176,0) 22%),
  transparent"></div>

<h2 class="abs display section-title" style="top:724px"><span>Why Choose Us</span></h2>

<div class="abs arrow" style="left:92px;top:920px"><svg width="12" height="12"><path d="M8 1 L3 6 L8 11" fill="none" stroke="#999" stroke-width="2"/></svg></div>
<div class="abs arrow" style="left:1075px;top:920px"><svg width="12" height="12"><path d="M4 1 L9 6 L4 11" fill="none" stroke="#999" stroke-width="2"/></svg></div>

<div class="abs feature" style="left:119px;top:854px">
  <div class="ring"><svg width="90" height="90" viewBox="0 0 90 90" fill="none" stroke="#34c83a" stroke-width="3"><circle cx="38" cy="28" r="14"/><path d="M14 84 V70 Q14 52 38 52 Q62 52 62 70 V84"/><circle cx="70" cy="66" r="14"/></svg></div>
  Professionally made<br>by a qualified dental<br>prosthetist
</div>
<div class="abs feature" style="left:368px;top:854px">
  <div class="ring orange"><svg width="80" height="80" viewBox="0 0 80 80" fill="none" stroke="#ee5f24" stroke-width="7"><path d="M10 12 V38 Q10 70 40 70 Q70 70 70 38 V12"/><path d="M26 12 V38 Q26 52 40 52 Q54 52 54 38 V12"/></svg></div>
  Custom fit for comfort,<br>protection, &amp; durability
</div>
<div class="abs feature" style="left:619px;top:854px">
  <div class="ring"><svg width="80" height="80" viewBox="0 0 80 80" fill="none" stroke="#34c83a" stroke-width="3"><rect x="8" y="10" width="18" height="60"/><path d="M26 30 L46 18 L56 34 L26 52"/><rect x="8" y="48" width="66" height="22"/></svg></div>
  Wide range of colours<br>and designs
</div>
<div class="abs feature" style="left:845px;top:854px">
  <div class="ring orange"><svg width="84" height="84" viewBox="0 0 84 84" fill="none" stroke="#ee5f24" stroke-width="4"><circle cx="42" cy="46" r="28"/><circle cx="33" cy="42" r="2" fill="#ee5f24"/><circle cx="51" cy="42" r="2" fill="#ee5f24"/><path d="M32 56 Q42 64 52 56"/><path d="M36 18 Q42 8 50 16"/></svg></div>
  Available for kids,<br>teens, and adults
</div>

<svg class="abs" style="left:0;top:1212px" width="1200" height="490" viewBox="0 0 1200 490">
  <defs><linearGradient id="aboutBand" x1="0" y1="0" x2="0" y2="1"><stop offset="0" stop-color="#0a2e6a"/><stop offset="0.55" stop-color="#1c8a48"/><stop offset="1" stop-color="#34c83a"/></linearGradient></defs>
  <path d="M0 0 H850 Q960 0 1000 60 V482 H0 Z" fill="url(#aboutBand)"/>
  <path d="M1050 60 A200 200 0 0 1 1000 410" fill="none" stroke="#34c83a" stroke-width="5"/>
  <path d="M1065 75 A205 205 0 0 1 1010 420" fill="none" stroke="#34c83a" stroke-width="4"/>
</svg>

<h2 class="abs display about-title">About Us</h2>
<div class="abs about-rule"></div>
<p class="abs about-copy">With over 20 years experience in the industry, our dental prosthetists take care to provide mouthguards that are made with precision and shaped for your comfort and protection. We are pleased to provide “gap free” mouthguards to all private health fund members with dental coverage, meaning you won’t have any out of pocket expenses.</p>
<div class="abs btn" style="left:142px;top:1547px;width:172px;height:54px">Read More</div>

<div class="abs" role="img" aria-label="Close-up of a white mouthguard with a team mascot print on a green background" style="left:719px;top:1256px;width:404px;height:404px;border-radius:50%;border:8px solid var(--white);background:
  radial-gradient(ellipse 120px 60px at 48% 22%,#ffffff 0,#eef1ee 60%,rgba(238,241,238,0) 100%),
  radial-gradient(ellipse 70px 140px at 72% 48%,#ffffff 0,#e9ece9 60%,rgba(233,236,233,0) 100%),
  radial-gradient(circle at 30% 30%,#2f4a48 0,rgba(47,74,72,0) 7%),
  radial-gradient(circle at 72% 58%,#2f4a48 0,rgba(47,74,72,0) 7%),
  linear-gradient(160deg,#7ee07a 0%,#46c446 50%,#2f9e34 100%)"></div>
<div class="abs" role="img" aria-label="Photo of a smiling woman holding clear mouthguards" style="left:857px;top:1566px;width:206px;height:206px;border-radius:50%;border:8px solid var(--white);background:
  radial-gradient(ellipse 50px 62px at 50% 38%,#e9c2a6 0,#deb093 70%,rgba(222,176,147,0) 100%),
  radial-gradient(ellipse 70px 40px at 50% 12%,#2a2320 0,rgba(42,35,32,0) 100%),
  linear-gradient(180deg,#d9dfe2 0%,#eceff0 60%,#ffffff 100%)"></div>

<div class="abs" role="img" aria-label="Faded photo of a child wearing a blue mouthguard and hands holding a clear mouthguard" style="left:0;top:2150px;width:1200px;height:620px;background:
  radial-gradient(ellipse 200px 260px at 80px 260px,rgba(236,205,175,.75),rgba(255,255,255,0) 100%),
  radial-gradient(ellipse 80px 40px at 115px 385px,rgba(90,170,230,.7),rgba(255,255,255,0) 100%),
  radial-gradient(ellipse 320px 160px at 1010px 540px,rgba(240,215,200,.7),rgba(255,255,255,0) 100%),
  linear-gradient(180deg,#ffffff 0%,#fbfaf8 100%)"></div>

<h2 class="abs display section-title" style="top:1807px"><span>Our Gallery</span></h2>

<div class="abs tile" role="img" aria-label="Glitter mouthguard in a purple case" style="left:143px;top:1912px;background:
  radial-gradient(ellipse 110px 40px at 48% 62%,#f2eef6 0,#d8d0e6 60%,rgba(216,208,230,0) 100%),
  linear-gradient(170deg,#7048c4 0%,#8a62d2 40%,#c9c3d2 70%,#e4e2e6 100%)"></div>
<div class="abs tile" role="img" aria-label="Teal mouthguard in a purple case" style="left:453px;top:1912px;background:
  radial-gradient(ellipse 120px 40px at 50% 60%,#3fbfa8 0,#2fa392 60%,rgba(47,163,146,0) 100%),
  linear-gradient(170deg,#6a4cbc 0%,#8062c8 40%,#c8c4d0 70%,#e6e4e8 100%)"></div>
<div class="abs" style="left:577px;top:2030px;width:48px;height:48px;border-radius:50%;background:var(--orange);color:var(--white);font-size:28px;display:flex;align-items:center;justify-content:center">+</div>
<div class="abs tile" role="img" aria-label="Several chequered and glitter mouthguards" style="left:761px;top:1912px;background:
  radial-gradient(ellipse 70px 50px at 30% 20%,#c9b6e2 0,rgba(201,182,226,0) 100%),
  radial-gradient(ellipse 80px 60px at 40% 62%,#e0607c 0,rgba(224,96,124,0) 100%),
  radial-gradient(ellipse 60px 90px at 80% 55%,#2a8fc8 0,rgba(42,143,200,0) 100%),
  radial-gradient(ellipse 60px 50px at 60% 88%,#1d7ab0 0,rgba(29,122,176,0) 100%),
  linear-gradient(180deg,#d8d4d0,#bfbab4)"></div>
<div class="abs tile" role="img" aria-label="Blue glitter mouthguard material discs" style="left:143px;top:2210px;background:
  radial-gradient(circle at 45% 35%,#6fc0e6 0,#2f8cc6 35%,#1f5f9a 52%,rgba(31,95,154,0) 54%),
  radial-gradient(circle at 45% 125%,#2f7fc0 0,#1d5a96 45%,rgba(29,90,150,0) 47%),
  linear-gradient(180deg,#9a6a44,#7a4e30)"></div>
<div class="abs tile" role="img" aria-label="Dark and pink mouthguards in red and white cases" style="left:453px;top:2210px;background:
  radial-gradient(ellipse 50px 90px at 28% 50%,#3a2a20 0,rgba(58,42,32,0) 100%),
  radial-gradient(ellipse 50px 90px at 70% 55%,#e8a0a8 0,rgba(232,160,168,0) 100%),
  linear-gradient(90deg,#c01c1c 0,#d22a22 48%,#ecebea 52%,#dcd6d6 100%)"></div>
<div class="abs tile" role="img" aria-label="Purple chequered mouthguard in a purple case" style="left:761px;top:2210px;background:
  radial-gradient(ellipse 110px 40px at 52% 60%,#d8d2f0 0,#8c7ad4 60%,rgba(140,122,212,0) 100%),
  linear-gradient(170deg,#5a3fb6 0%,#7a5ccc 40%,#c8c4d0 70%,#e6e4e8 100%)"></div>

<div class="abs btn" style="left:506px;top:2546px;width:188px;height:66px">View More</div>

<svg class="abs" style="left:0;top:2680px" width="1200" height="477" viewBox="0 0 1200 477">
  <path d="M0 130 Q600 -70 1200 130 V477 H0 Z" fill="#0a1a5c"/>
  <path d="M0 130 Q600 -70 1200 130" fill="none" stroke="#34c83a" stroke-width="8"/>
</svg>

<div class="abs foot-info" style="left:226px">
  <span class="ic"><svg width="14" height="18" viewBox="0 0 14 18"><path d="M7 1 A6 6 0 0 1 13 7 C13 11 7 17 7 17 C7 17 1 11 1 7 A6 6 0 0 1 7 1Z" fill="#0a1a5c"/><circle cx="7" cy="7" r="2" fill="#fff"/></svg></span>
  <span>Unit 4/12 Meridian Way,<br>Kestrel WA 6091</span>
</div>
<div class="abs foot-info" style="left:486px;font-size:17px;font-weight:500">
  <span class="ic hot"><svg width="16" height="16" viewBox="0 0 16 16"><path d="M3 1 L6 1 L7 5 L5 6 Q6 9 10 11 L11 9 L15 10 L15 13 Q15 15 12 15 Q2 13 1 4 Q1 1 3 1Z" fill="#fff"/></svg></span>
  <span>08 6100 2417</span>
</div>
<div class="abs foot-info" style="left:685px">
  <span class="ic"><svg width="16" height="12" viewBox="0 0 16 12"><rect x="0" y="0" width="16" height="12" rx="1" fill="#0a1a5c"/><path d="M1 1 L8 7 L15 1" fill="none" stroke="#fff" stroke-width="1.4"/></svg></span>
  <span>reception@harbourlinedental.com.au</span>
</div>

<div class="abs foot-nav">HOME<span>/</span>ABOUT US<span>/</span>OUR MOUTHGUARDS<span>/</span>GALLERY<span>/</span>FAQ<span>/</span>CONTACT</div>
<div class="abs legal">© 2025 Companyname.All Rights Reserved &nbsp;|&nbsp; Privacy Policy &nbsp;|&nbsp; Terms of Use</div>
<div class="abs social" aria-label="Social media links"><i></i><i></i><i></i><i></i><i></i></div>
<div class="abs partner">HARBOURLINE DENTURE CARE</div>

</body>
</html>
```